Income Tax Business Cards - Updates

Need to update these business cards while keeping all the same wording but just update them and make them look nicer and more modern/ on brand with our brand.

Industry/Entity Type

finance

Contact Information for Business Card

we have multiple locations so will just need to easily be able to change the address and phone numbers

Colors

Designer to choose colors to be used in the design.

```html
<!DOCTYPE html>
<html lang="en">
<head>
<meta charset="utf-8">
<title>Ledgerline Financial Group – Business Cards</title>
<link rel="stylesheet" href="https://fonts.googleapis.com/css2?family=Tinos:wght@400;700&family=Arimo:wght@400;700&display=swap">
<style>
  :root {
    --green: #0f4f2c;
    --red: #b31d24;
    --white: #ffffff;
    --paper: #f4f4f4;
    --ink: #1b1b1b;
    --stage: #e6e6e6;
  }
  * { margin: 0; padding: 0; box-sizing: border-box; }
  html, body { width: 1200px; height: 912px; overflow: hidden; background: var(--stage); }
  .canvas { position: relative; width: 1200px; height: 912px; }
  .card {
    position: absolute; left: 250px; width: 700px; height: 400px;
    border-radius: 26px; overflow: hidden;
    box-shadow: 0 6px 18px rgba(0,0,0,.18);
  }
  .card-front { top: 40px; background: var(--green); color: var(--white); }
  .card-back { top: 472px; background: var(--paper); }

  .brand { font-family: "Tinos", serif; font-weight: 700; line-height: 1; white-space: nowrap; }
  .brand-mark { display: inline-block; width: 14px; height: 14px; margin-right: 10px; vertical-align: middle; }

  .front-brand { position: absolute; top: 40px; width: 100%; text-align: center; font-size: 34px; color: var(--white); }
  .front-brand .brand-mark { background: var(--white); }
  .front-brand small { display: block; font-size: 13px; letter-spacing: 4px; margin-top: 8px; font-weight: 400; }

  .band {
    position: absolute; top: 160px; left: 0; width: 100%; height: 70px;
    background: var(--red); display: flex; align-items: center; justify-content: center;
    font-family: "Tinos", serif; font-weight: 700; font-size: 50px; color: var(--white);
  }
  .front-amount {
    position: absolute; top: 248px; width: 100%; text-align: center;
    font-family: "Arimo", sans-serif; font-weight: 700; font-size: 72px; line-height: 1;
  }
  .front-tagline {
    position: absolute; top: 326px; width: 100%; text-align: center;
    font-family: "Tinos", serif; font-weight: 700; font-size: 46px; line-height: 1;
  }

  .back-curve { position: absolute; inset: 0; }
  .back-brand { position: absolute; top: 112px; left: 40px; font-size: 34px; color: var(--green); }
  .back-brand .brand-mark { background: var(--red); }
  .back-brand small { display: block; font-size: 12px; letter-spacing: 4px; margin-top: 8px; margin-left: 24px; font-weight: 400; }
  .phone {
    position: absolute; top: 186px; left: 40px; line-height: 1; white-space: nowrap;
    font-family: "Arimo", sans-serif; font-weight: 700; font-size: 42px; color: var(--ink);
  }
  .offer { position: absolute; top: 26px; left: 330px; width: 340px; text-align: center; }
  .offer-title {
    font-family: "Tinos", serif; font-weight: 700; font-size: 27px; line-height: 1.1;
    color: var(--green); letter-spacing: .5px; white-space: nowrap;
  }
  .offer-note { font-family: "Arimo", sans-serif; font-size: 16px; color: var(--red); margin-top: 2px; }
  .estimates {
    display: inline-block; margin-top: 10px; padding: 5px 18px;
    background: var(--red); border-radius: 8px; white-space: nowrap;
    font-family: "Tinos", serif; font-weight: 700; font-size: 28px; line-height: 1.2; color: var(--white);
  }
  .address {
    position: absolute; top: 180px; left: 372px; padding-left: 12px;
    border-left: 2px solid var(--red); white-space: nowrap;
    font-family: "Arimo", sans-serif; font-size: 16px; line-height: 1.35; color: var(--ink);
  }
  .back-amount {
    position: absolute; right: 36px; bottom: 30px; line-height: 1; white-space: nowrap;
    font-family: "Arimo", sans-serif; font-weight: 700; font-size: 60px; color: var(--white);
  }
</style>
</head>
<body>
<main class="canvas">
  <section class="card card-front">
    <div class="brand front-brand"><span class="brand-mark"></span>Ledgerline<small>FINANCIAL GROUP</small></div>
    <div class="band">File your Taxes here</div>
    <div class="front-amount">UP to $6000</div>
    <div class="front-tagline">Same day advance</div>
  </section>

  <section class="card card-back">
    <svg class="back-curve" width="700" height="400" viewBox="0 0 700 400" aria-hidden="true">
      <path d="M150 400 C 260 280, 430 250, 700 235 L700 400 Z" fill="var(--red)"/>
      <path d="M172 400 C 276 292, 440 264, 700 251 L700 400 Z" fill="var(--green)"/>
    </svg>
    <div class="brand back-brand"><span class="brand-mark"></span>Ledgerline<small>FINANCIAL GROUP</small></div>
    <div class="phone">(555) 555-5555</div>
    <div class="offer">
      <div class="offer-title">SAME DAY ADVANCE</div>
      <div class="offer-note">on approved tax returns!</div>
      <div class="estimates">FREE ESTIMATES!</div>
    </div>
    <div class="address">2190 Harborview Lane<br>Elmont, NY 11003</div>
    <div class="back-amount">UP to $6000</div>
  </section>
</main>
</body>
</html>
```